Brightgate Audio Video Security LLC

Need help designing a web page for an alarm company. I want to promote my business.

Target Market(s)

Residential and commercial clients

Industry/Entity Type

Security Service

Coding

Coded - Design and coding required

Number of Pages Required

2 page

Font styles to use
Sans Serif

Requirements
Must have
• I would llike my logo displayed on the page. I would like my slogan displayed as well
´´A GREAT PLACE FOR YOUR SECURITY NEEDS´´
We are licensed and insured
Company phone number 832-555-0147
Company hours: Monday-Friday 8am-5pm Company address: P.O. Box 419 Crosby, TX 77519 over 25 years experience
Email info. Brightgatesys@kelvamail.com
Company license #K41862509
Fire license# MTQ-6071852
LUV-8146027
We offer alarm monitoring,security cameras, access control,gate openers, home theater systems, covert camera installations, FIre alarm installation and monitoring
Nice to have
• We offer security at competitive prices.
Get customer information for a free quote similar to qmr website.
Should not have
• No prices listed on website

```html
<!DOCTYPE html>
<html lang="en">
<head>
<meta charset="utf-8">
<title>Brightgate Audio Video Security</title>
<link rel="stylesheet" href="https://fonts.googleapis.com/css2?family=Barlow+Condensed:wght@400;500;600;700&family=Mulish:wght@400;600&display=swap">
<style>
:root{
  --red:#9b0f24;
  --red-bright:#d9112d;
  --red-hero:#8a1326;
  --ink:#222;
  --text:#555;
  --grey-bg:#ececec;
  --line:#c9c9c9;
  --black:#000;
  --white:#fff;
  --head:"Barlow Condensed",sans-serif;
  --body:"Mulish",sans-serif;
}
*{margin:0;padding:0;box-sizing:border-box}
html,body{width:1200px;height:3524px;overflow:hidden}
body{position:relative;background:var(--white);font-family:var(--body);color:var(--text)}
.abs{position:absolute}
.brand{font-family:var(--head);font-weight:700;letter-spacing:1px;display:flex;align-items:center;gap:8px}
.brand .dot{width:14px;height:14px;border-radius:50%;background:currentColor}
.header{top:0;left:0;width:1200px;height:95px;background:var(--white)}
.header .brand{position:absolute;left:111px;top:30px;font-size:32px;color:var(--red-bright)}
.nav{position:absolute;right:114px;top:0;display:flex;gap:31px;height:95px;align-items:center}
.nav a{font-family:var(--head);font-size:15px;color:#777;text-decoration:none;letter-spacing:.3px;height:95px;line-height:122px;position:relative}
.nav a.active{color:var(--red-bright)}
.nav a.active::after{content:"";position:absolute;left:0;right:0;bottom:2px;height:2px;background:var(--red-bright)}
.hero{top:95px;left:0;width:1200px;height:556px;background:linear-gradient(120deg,#4a4640 0%,#6e6a62 45%,#3d3a35 100%)}
.hero-panel{position:absolute;left:0;top:0;width:599px;height:556px;background:linear-gradient(160deg,rgba(150,20,40,.95),rgba(130,16,36,.93))}
.hero h1{position:absolute;left:111px;top:130px;font-family:var(--head);font-weight:600;font-size:51px;line-height:56px;color:var(--white)}
.hero p{position:absolute;left:111px;top:258px;width:330px;font-size:15px;line-height:26px;color:var(--white)}
.btn{display:inline-block;font-family:var(--head);font-weight:600;color:var(--white);text-transform:uppercase;text-align:center}
.hero .btn{position:absolute;left:111px;top:374px;width:131px;height:45px;line-height:45px;background:var(--red-bright);font-size:16px}
.dots{display:flex;gap:4px}
.dots span{width:8px;height:8px;border-radius:50%;background:var(--white)}
.dots span.on{background:var(--red-bright)}
.hero .dots{position:absolute;left:585px;top:523px}
h2{font-family:var(--head);font-weight:500;font-size:33px;color:var(--ink)}
.rule{width:86px;height:1px;background:var(--red-bright)}
.about{top:738px;left:0;width:1200px;text-align:center}
.about .rule{margin:12px auto 0}
.about p{width:840px;margin:28px auto 0;font-size:15px;line-height:26px}
.about .btn{margin-top:28px;width:99px;height:40px;line-height:40px;background:var(--red);font-size:15px}
.services{top:1071px;left:0;width:1200px;height:513px;background:var(--grey-bg)}
.services h2{position:absolute;top:88px;width:1200px;text-align:center}
.services .rule{position:absolute;top:138px;left:557px}
.card{position:absolute;top:172px;width:229px;height:210px;background:var(--white);border:1px solid #aaa;text-align:center}
.card svg{margin-top:14px}
.card h3{font-family:var(--head);font-weight:500;font-size:16px;color:var(--ink);margin-top:6px}
.card .rule{position:static;width:52px;margin:10px auto 0}
.card p{font-size:12px;line-height:26px;margin:12px 18px 0}
.services .dots{position:absolute;left:584px;top:412px}
.services .dots span{background:var(--ink)}
.services .dots span.on{background:var(--red-bright)}
.adv-photo{top:1680px;left:101px;width:489px;height:375px;background:linear-gradient(135deg,#6b6a5e,#3e3a33 55%,#7a5a48)}
.adv-text{top:1685px;left:680px;width:420px}
.adv-text h2{font-size:33px}
.adv-text .rule{margin-top:16px;width:106px}
.adv-text p{margin-top:28px;font-size:15px;line-height:26px;text-align:justify}
.adv-text .btn{margin-top:36px;width:103px;height:41px;line-height:41px;background:var(--red);font-size:16px}
.video{top:2150px;left:0;width:1200px;height:355px;background:linear-gradient(100deg,#b7283e 0%,#9a1630 50%,#7e0f22 100%);text-align:center;color:var(--white)}
.video h2{color:var(--white);margin-top:94px;font-size:35px}
.video .rule{margin:10px auto 0;width:100px;background:rgba(255,255,255,.6)}
.video p{width:680px;margin:16px auto 0;font-size:15px;line-height:26px}
.video svg{margin-top:14px}
.contact-card{top:2605px;left:125px;width:387px;height:382px;border:9px solid #d3d3d3;text-align:center}
.contact-card h2{margin-top:54px;font-size:34px;font-weight:600}
.contact-card .phone{font-family:var(--head);font-weight:600;font-size:33px;color:var(--red);margin-top:2px}
.contact-card h4{font-family:var(--head);font-weight:600;font-size:16px;color:var(--ink);margin-top:26px}
.contact-card p{font-size:17px;line-height:25px;margin-top:4px}
.field{position:absolute;height:46px;border:1px solid #aaa;font-size:13px;color:#666;padding:14px 12px;display:flex;justify-content:space-between}
.field svg{flex:none}
.submit{top:2898px;left:569px;width:103px;height:42px;line-height:42px;background:var(--red);font-size:16px}
.footer{top:3115px;left:0;width:1200px;height:409px;background:var(--black);color:var(--white)}
.footer .brand{position:absolute;left:132px;top:130px;font-size:38px;color:var(--white)}
.lic{position:absolute;top:228px;font-family:var(--head);font-weight:600;font-size:16px}
.lic span{display:block;font-family:var(--body);font-weight:400;font-size:17px;margin-top:6px}
.fcol{position:absolute;top:88px}
.fcol h5{font-family:var(--head);font-weight:600;font-size:15px;letter-spacing:.3px}
.fcol ul{list-style:none;margin-top:28px}
.fcol li{font-size:15px;line-height:26px}
.sub-input{position:absolute;left:903px;top:134px;width:201px;height:37px;background:var(--white);color:#777;font-size:12px;padding:11px 10px}
.sub-btn{position:absolute;left:903px;top:185px;width:201px;height:37px;line-height:37px;background:var(--red);font-size:15px}
.fline{position:absolute;left:83px;top:309px;width:1031px;height:1px;background:#666}
.copy{position:absolute;right:86px;top:323px;font-family:var(--head);font-size:11px}
.social{position:absolute;top:331px;left:88px;display:flex;gap:9px}
.social span{width:34px;height:34px;border-radius:50%;background:#1e1e1e;display:flex;align-items:center;justify-content:center}
.social i{width:8px;height:8px;background:var(--white);border-radius:2px}
</style>
</head>
<body>

<header class="header abs">
  <div class="brand"><span class="dot"></span>BRIGHTGATE</div>
  <nav class="nav">
    <a class="active">HOME</a><a>ABOUT US</a><a>SERVICES</a><a>WHY BRIGHTGATE</a><a>NEWS</a><a>CONTACT US</a>
  </nav>
</header>

<section class="hero abs" role="img" aria-label="Close-up photo of a wall-mounted security camera">
  <div class="hero-panel"></div>
  <h1>A GREAT PLACE FOR YOUR<br>SECURITY NEEDS</h1>
  <p>Lorem ipsum dolor sit amet, consectetur adipiscing elit, sed do eiusmod tempor incididunt ut labore et dolore magna aliqua.</p>
  <span class="btn">Get Started</span>
  <div class="dots"><span class="on"></span><span></span><span></span></div>
</section>

<section class="about abs">
  <h2>About Brightgate</h2>
  <div class="rule"></div>
  <p>Lorem ipsum dolor sit amet, consectetur adipiscing elit, sed do eiusmod tempor incididunt ut labore et dolore magna aliqua. Ut enim ad minim veniam, quis nostrud exercitation ullamco laboris nisi ut aliquip ex ea commodo consequat. Duis aute irure dolor in reprehenderit in voluptate velit esse cillum dolore eu fugiat nulla pariatur. Excepteur sint occaecat cupidatat non proident, sunt in culpa qui officia deserunt mollit anim id est laborum.</p>
  <span class="btn">Read More</span>
</section>

<section class="services abs">
  <h2>Our Services</h2>
  <div class="rule"></div>
  <div class="card" style="left:115px">
    <svg width="48" height="44" viewBox="0 0 48 44" fill="none" stroke="#333" stroke-width="2"><rect x="6" y="6" width="36" height="26"/><path d="M2 36h44l-3 5H5z"/><path d="M17 27c3-3 2-12 7-13 5 1 4 10 7 13z"/><circle cx="24" cy="11" r="2"/></svg>
    <h3>Alarm Monitoring</h3><div class="rule"></div>
    <p>Lorem ipsum dolor sit amet, consectetur adipiscing elit, sed do eiusmod tempor.</p>
  </div>
  <div class="card" style="left:361px">
    <svg width="48" height="44" viewBox="0 0 48 44" fill="none" stroke="#333" stroke-width="2"><path d="M14 12l28 10-4 8-28-10z"/><path d="M16 22l-3 8H6"/><path d="M4 24v16"/><path d="M30 28l6 4"/></svg>
    <h3>Security Cameras</h3><div class="rule"></div>
    <p>Lorem ipsum dolor sit amet, consectetur adipiscing elit, sed do eiusmod tempor.</p>
  </div>
  <div class="card" style="left:608px">
    <svg width="48" height="44" viewBox="0 0 48 44" fill="none" stroke="#333" stroke-width="2"><rect x="17" y="12" width="14" height="30" rx="3"/><circle cx="24" cy="19" r="2"/><path d="M21 26h6M21 31h6M21 36h6"/><path d="M18 7a9 9 0 0 1 12 0M20 3a12 12 0 0 1 8 0"/></svg>
    <h3>Access Control</h3><div class="rule"></div>
    <p>Lorem ipsum dolor sit amet, consectetur adipiscing elit, sed do eiusmod tempor.</p>
  </div>
  <div class="card" style="left:855px">
    <svg width="56" height="44" viewBox="0 0 56 44" fill="none" stroke="#333" stroke-width="2"><rect x="2" y="6" width="8" height="34"/><rect x="46" y="6" width="8" height="34"/><rect x="14" y="8" width="28" height="18"/><path d="M14 32h28v8H14z"/><circle cx="6" cy="14" r="2"/><circle cx="50" cy="14" r="2"/></svg>
    <h3>Home Theater Systems</h3><div class="rule"></div>
    <p>Lorem ipsum dolor sit amet, consectetur adipiscing elit, sed do eiusmod tempor.</p>
  </div>
  <div class="dots"><span class="on"></span><span></span><span></span></div>
</section>

<div class="adv-photo abs" role="img" aria-label="Photo of an outdoor security camera mounted under a roof edge"></div>
<section class="adv-text abs">
  <h2>Advantage Of Brightgate</h2>
  <div class="rule"></div>
  <p>Lorem ipsum dolor sit amet, consectetur adipiscing elit, sed do eiusmod tempor incididunt ut labore et dolore magna aliqua. Ut enim ad minim veniam, quis nostrud exercitation ullamco laboris nisi ut aliquip ex ea commodo consequat. Duis aute irure dolor in reprehenderit in voluptate velit esse cillum dolore eu fugiat nulla pariatur. Excepteur sint occaecat cupidatat non proident, sunt in culpa qui officia deserunt mollit anim id est laborum.</p>
  <span class="btn">Read More</span>
</section>

<section class="video abs" role="img" aria-label="Red-tinted photo of a security camera behind the demo video call-out">
  <h2>Watch Our Demo Video</h2>
  <div class="rule"></div>
  <p>Lorem ipsum dolor sit amet, consectetur adipiscing elit, sed do eiusmod tempor incididunt ut labore et dolore magna aliqua.</p>
  <svg width="44" height="44" viewBox="0 0 44 44" fill="none" stroke="#fff" stroke-width="3"><circle cx="22" cy="22" r="19"/><path d="M17 13l13 9-13 9z" fill="#fff"/></svg>
</section>

<section class="contact-card abs">
  <h2>Get In Touch</h2>
  <div class="phone">832-555-0147</div>
  <h4>Address</h4>
  <p>P.O. Box 419 Crosby,<br>TX 77519</p>
  <h4>Email</h4>
  <p>Brightgatesys@kelvamail.com</p>
</section>

<form>
  <div class="field" style="left:569px;top:2651px;width:249px">Name<svg width="11" height="12" viewBox="0 0 11 12"><circle cx="5.5" cy="3.5" r="3" fill="#666"/><path d="M0 12c0-4 11-4 11 0z" fill="#666"/></svg></div>
  <div class="field" style="left:828px;top:2651px;width:249px">Email<svg width="13" height="10" viewBox="0 0 13 10"><rect width="13" height="10" fill="#666"/><path d="M0 1l6.5 5L13 1" stroke="#fff" fill="none"/></svg></div>
  <div class="field" style="left:569px;top:2712px;width:249px">Address<svg width="9" height="12" viewBox="0 0 9 12"><path d="M4.5 12C1 7 0 6 0 4.5a4.5 4.5 0 0 1 9 0C9 6 8 7 4.5 12z" fill="#666"/><circle cx="4.5" cy="4.5" r="1.6" fill="#fff"/></svg></div>
  <div class="field" style="left:828px;top:2712px;width:249px">Phone<svg width="11" height="11" viewBox="0 0 11 11"><path d="M2 0l2 3-1 1.5c1 2 2 3 3.5 3.5L8 7l3 2-1.5 2C5 11 0 6 0 1.5z" fill="#666"/></svg></div>
  <div class="field" style="left:569px;top:2773px;width:506px;height:88px">Message<svg width="13" height="11" viewBox="0 0 13 11"><ellipse cx="6.5" cy="4.5" rx="6.5" ry="4.5" fill="#666"/><path d="M2 7l-1 4 4-2.5z" fill="#666"/></svg></div>
  <span class="btn submit abs">Submit</span>
</form>

<footer class="footer abs">
  <div class="brand"><span class="dot"></span>BRIGHTGATE</div>
  <div class="lic" style="left:125px">Company license<span>#K41862509</span></div>
  <div class="lic" style="left:297px">Fire license<span># MTQ-6071852</span></div>
  <div class="fcol" style="left:474px"><h5>INFORMATION</h5><ul><li>Home</li><li>About Us</li><li>Services</li><li>Why Brightgate</li><li>News</li><li>Contact Us</li></ul></div>
  <div class="fcol" style="left:697px"><h5>HELPFUL LINKS</h5><ul><li>Company license</li><li>Fire license</li><li>Terms &amp; Condition</li><li>Privacy Policy</li></ul></div>
  <div class="fcol" style="left:903px"><h5>HELPFUL LINKS</h5></div>
  <div class="sub-input">Enter The Email</div>
  <span class="btn sub-btn">Subscribe</span>
  <div class="fline"></div>
  <div class="copy">© Copyrights 2020 &nbsp;Brightgate &nbsp;| &nbsp;All Rights Reserved</div>
  <div class="social"><span><i></i></span><span><i></i></span><span><i></i></span><span><i></i></span></div>
</footer>

</body>
</html>
```